Business cards for Harbourline Supply Pty Ltd that import building products into Australia from China
Target Market(s)
Business to Business
Industry/Entity Type
Business
Contact Information for Business Card
Front: Logo and Business Name
Rear:
Desmond Varrick
General Manager
Mobile: 0427 561 394
email: dessie@harbourlinesupply.com.au
alternative email: dessie@outbackworks.com.au
web: www.harbourlinesupply.com.au
Adelaide, Brisbane and Darwin
Colors
ec1f27
fbee3d

```html
<!DOCTYPE html>
<html lang="en">
<head>
<meta charset="utf-8">
<title>Harbourline Supply – Business Cards</title>
<link rel="stylesheet" href="https://fonts.googleapis.com/css2?family=PT+Sans:wght@400;700&display=swap">
<style>
  :root {
    --backdrop: #b3b3b3;
    --card-light: #f2f2f2;
    --card-dark: #252525;
    --ink: #1f1f1f;
    --brand-red: #ec1f27;
    --brand-yellow: #fbee3d;
    --white: #ffffff;
  }
  * { margin: 0; padding: 0; box-sizing: border-box; }
  html, body { width: 1200px; height: 900px; overflow: hidden; }
  body {
    position: relative;
    background: var(--backdrop);
    font-family: "PT Sans", "Myriad Pro", Arial, sans-serif;
    color: var(--ink);
  }
  .card {
    position: absolute;
    top: 170px;
    width: 347px;
    height: 561px;
    overflow: hidden;
  }
  .card--contact { left: 259px; background: var(--card-light); }
  .card--brand { left: 631px; background: var(--card-dark); }

  /* Name lockup: invented name with one plain square */
  .brand-lockup {
    position: absolute;
    left: 0; right: 0;
    display: flex;
    align-items: center;
    justify-content: center;
    gap: 12px;
  }
  .brand-lockup__square {
    background: var(--brand-yellow);
    flex: none;
  }
  .brand-lockup__name {
    font-weight: 700;
    line-height: 1.08;
    text-align: left;
    white-space: nowrap;
  }
  .card--contact .brand-lockup { top: 128px; height: 44px; }
  .card--contact .brand-lockup__square { width: 34px; height: 34px; }
  .card--contact .brand-lockup__name { font-size: 30px; color: var(--ink); }

  .card--brand .brand-lockup { top: 246px; height: 72px; }
  .card--brand .brand-lockup__square { width: 38px; height: 38px; }
  .card--brand .brand-lockup__name { font-size: 31px; color: var(--white); }

  .person__name {
    position: absolute;
    top: 320px;
    left: 0; right: 0;
    text-align: center;
    font-size: 21px;
    font-weight: 400;
    letter-spacing: 0.2px;
    line-height: 22px;
  }
  .person__surname { color: var(--brand-red); }
  .person__role {
    position: absolute;
    top: 345px;
    left: 0; right: 0;
    text-align: center;
    font-size: 16px;
    line-height: 20px;
  }

  .contact-list {
    position: absolute;
    top: 391px;
    left: 0; right: 0;
    list-style: none;
    text-align: center;
    font-size: 16px;
    line-height: 25.5px;
  }
  .contact-list__label {
    color: var(--brand-red);
    font-weight: 700;
  }
  .contact-list__web { font-weight: 700; }
  .contact-list__web-accent { color: var(--brand-red); }

  .locations {
    position: absolute;
    top: 513px;
    left: 0; right: 0;
    text-align: center;
    font-size: 16px;
    line-height: 20px;
  }
</style>
</head>
<body>
  <section class="card card--contact" aria-label="Business card, contact side">
    <div class="brand-lockup">
      <span class="brand-lockup__square"></span>
      <span class="brand-lockup__name">Harbourline Supply</span>
    </div>

    <h1 class="person__name">DESMOND <span class="person__surname">VARRICK</span></h1>
    <p class="person__role">General Manager</p>

    <ul class="contact-list">
      <li><span class="contact-list__label">M:</span> 0427 561 394</li>
      <li><span class="contact-list__label">E:</span> dessie@harbourlinesupply.com.au</li>
      <li><span class="contact-list__label">E:</span> dessie@outbackworks.com.au</li>
      <li class="contact-list__web">www.<span class="contact-list__web-accent">harbourlinesupply</span>.com.au</li>
    </ul>

    <p class="locations">Adelaide, Brisbane and Darwin</p>
  </section>

  <section class="card card--brand" aria-label="Business card, brand side">
    <div class="brand-lockup">
      <span class="brand-lockup__square"></span>
      <span class="brand-lockup__name">Harbourline Supply<br>Pty Ltd</span>
    </div>
  </section>
</body>
</html>
```